Business card for my new company (Accounting firm)

I need a business card for my new business Brightwell Advisory and Ledger SA. Our services are accounting, tax, audit and financial management. Our customers are small companies, start-ups and new companies. The final design has to show financial security, trust and growth. Please find our logo attached to the business card. Text for the business card: Brightwell Advisory and Ledger SA Tomas Varenholt Director and Founder Certified Accountant Tel. 022 418 57 34 tv@clairevalconseil.ch www.clairevalconseil.ch Rue des Vergières 27 1201 Geneva
Target Market(s)
Our customers are small companies, start-ups and new companies.
Industry/Entity Type
Finance And Accounting
Contact Information for Business Card
Claireval Conseil et Comptes SA
Tomas Varenholt
Directeur et Fondateur
Expert-comptable diplômé
Tél. 022 418 57 34
tv@clairevalconseil.ch
www.clairevalconseil.ch
Rue des Vergières 27
1201 Genève

```html
<!DOCTYPE html>
<html lang="fr">
<head>
<meta charset="utf-8">
<title>Claireval Conseil et Comptes SA – carte de visite</title>
<link rel="stylesheet" href="https://fonts.googleapis.com/css2?family=Poppins:wght@400;500&display=swap">
<style>
  :root {
    --backdrop: #e6e7e9;
    --paper: #f4f4f5;
    --ink: #3a3c42;
    --ink-soft: #4a4c52;
    --brand-blue: #2c9fd6;
    --brand-blue-deep: #1b6fb5;
    --brand-navy: #1d5488;
    --back-light: #35b2dd;
    --back-mid: #2a9fd4;
    --back-deep: #1e7fc8;
    --white: #ffffff;
  }
  * { margin: 0; padding: 0; box-sizing: border-box; }
  html, body {
    width: 1105px; height: 1200px; overflow: hidden;
    background: var(--backdrop);
    font-family: "Poppins", sans-serif;
  }
  .canvas { position: relative; width: 1105px; height: 1200px; }

  .card {
    position: absolute; left: 182px; width: 747px;
    box-shadow: 0 10px 22px rgba(0,0,0,0.16);
  }
  .card--front { top: 118px; height: 427px; background: var(--paper); overflow: hidden; }
  .card--back { top: 635px; height: 429px; overflow: hidden; }

  .brand-block {
    position: absolute; left: 40px; width: 300px; top: 178px;
    display: flex; align-items: center; justify-content: center; gap: 12px;
  }
  .brand-block__square { width: 22px; height: 22px; background: var(--brand-blue); }
  .brand-block__name {
    font-weight: 500; font-size: 40px; color: var(--ink); letter-spacing: 0.5px; line-height: 1;
  }

  .divider {
    position: absolute; left: 351px; top: 110px; width: 1.5px; height: 206px; background: var(--ink);
  }

  .details { position: absolute; left: 387px; top: 102px; color: var(--ink-soft); }
  .details__name { font-size: 25px; font-weight: 500; color: var(--brand-blue); line-height: 1.2; }
  .details__role { font-size: 16.5px; line-height: 1.32; color: var(--ink); }
  .details__address { margin-top: 26px; font-size: 16.5px; font-weight: 400; line-height: 1.3; }
  .contact-list { list-style: none; margin-top: 22px; font-size: 16.5px; line-height: 1.3; }
  .contact-list li { display: flex; align-items: center; gap: 8px; margin-bottom: 0.5px; }
  .contact-list svg { width: 12px; height: 12px; flex: none; }

  .front-stripe {
    position: absolute; left: 0; bottom: 0; width: 100%; height: 8px;
    background: linear-gradient(90deg, var(--brand-navy), var(--brand-blue) 50%, var(--brand-navy));
  }

  .back-pattern {
    position: absolute; inset: 0;
    background: linear-gradient(100deg, var(--back-light) 0%, var(--back-mid) 45%, var(--back-deep) 100%);
  }
  .back-signature {
    position: absolute; right: 52px; bottom: 56px;
    font-size: 15px; font-weight: 500; color: var(--white);
  }
</style>
</head>
<body>
<main class="canvas">
  <section class="card card--front" aria-label="Recto de la carte">
    <div class="brand-block">
      <span class="brand-block__square"></span>
      <span class="brand-block__name">Claireval</span>
    </div>

    <div class="divider"></div>

    <div class="details">
      <p class="details__name">Tomas Varenholt</p>
      <p class="details__role">Directeur et Fondateur<br>Expert-comptable diplômé</p>
      <p class="details__address">Rue des Vergières 27<br>1201 Genève</p>
      <ul class="contact-list">
        <li>
          <svg viewBox="0 0 12 12" aria-hidden="true"><path fill="#2c9fd6" d="M2.4 0.8l1.8 0.2 0.8 2.4-1.2 1c0.7 1.4 1.6 2.3 3 3l1-1.2 2.4 0.8 0.2 1.8c-0.4 1-1.4 1.6-2.4 1.4C4.6 9.6 2.4 7.4 1 3.2 0.8 2.2 1.4 1.2 2.4 0.8z"/></svg>
          022 418 57 34
        </li>
        <li>
          <svg viewBox="0 0 12 12" aria-hidden="true"><rect x="0.5" y="2" width="11" height="8" rx="1" fill="#2c9fd6"/><path d="M1 2.6l5 3.8 5-3.8" stroke="#fff" stroke-width="1" fill="none"/></svg>
          tv@clairevalconseil.ch
        </li>
        <li>
          <svg viewBox="0 0 12 12" aria-hidden="true"><circle cx="6" cy="6" r="5.5" fill="#2c9fd6"/><path d="M0.8 6h10.4M6 0.6c-2 2.6-2 8.2 0 10.8M6 0.6c2 2.6 2 8.2 0 10.8" stroke="#fff" stroke-width="0.8" fill="none"/></svg>
          www.clairevalconseil.ch
        </li>
      </ul>
    </div>

    <div class="front-stripe"></div>
  </section>

  <section class="card card--back" aria-label="Verso de la carte">
    <div class="back-pattern" role="img" aria-label="Motif répété en relief du symbole de la marque sur fond bleu"></div>
    <span class="back-signature">Claireval</span>
  </section>
</main>
</body>
</html>
```